New Business Card Design Project

Use the flyer uploaded and website www.brightoakbuilders.com for inspiration.
List Our Services on Backside of business cards
Marcus Delling
Harborline Builders Inc.
Licensed General Contractors
858-471-6093

Contact Information for Business Card

Use the flyer uploaded and website www.brightoakbuilders.com for inspiration. List Our Services on Backside of business cards Marcus Delling Harborline Builders Inc. Licensed General Contractors 858-471-6093

```html
<!DOCTYPE html>
<html lang="en">
<head>
<meta charset="utf-8">
<title>Harborline Builders – Business Card</title>
<link rel="stylesheet" href="https://fonts.googleapis.com/css2?family=Cinzel:wght@400&family=Arimo:wght@400;700&display=swap">
<style>
  :root {
    --bg-top: #e4e4e4;
    --bg-bottom: #b9b9b9;
    --card-white: #f7f7f7;
    --card-dark: #3b3b3b;
    --ink: #1c1c1c;
    --ink-soft: #333333;
    --white: #ffffff;
  }
  * { box-sizing: border-box; margin: 0; padding: 0; }
  html, body { width: 1200px; height: 800px; overflow: hidden; }
  body {
    background: linear-gradient(180deg, var(--bg-top), var(--bg-bottom));
    font-family: "Arimo", Arial, sans-serif;
  }
  .canvas { position: relative; width: 1200px; height: 800px; }
  .card {
    position: absolute;
    top: 250px;
    width: 520px;
    height: 300px;
    border-radius: 18px;
    background: var(--card-white);
    overflow: hidden;
    box-shadow: 0 10px 24px rgba(0,0,0,.18);
  }
  .card--front { left: 50px; }
  .card--back { left: 630px; }

  .front-shapes { position: absolute; inset: 0; }

  .holder-name {
    position: absolute; top: 24px; right: 30px;
    font-family: "Cinzel", "Times New Roman", serif;
    font-weight: 400;
    font-size: 20px; letter-spacing: 1px; color: var(--white);
  }
  .contact-list {
    position: absolute; top: 176px; right: 18px;
    list-style: none; text-align: right;
    font-size: 12px; line-height: 18px; color: var(--ink-soft);
  }
  .contact-list li { display: flex; justify-content: flex-end; align-items: center; gap: 6px; }
  .contact-list svg { width: 11px; height: 11px; flex: none; }

  .brand {
    position: absolute; left: 34px; top: 126px;
    display: flex; align-items: center; gap: 10px;
    font-family: "Cinzel", "Times New Roman", serif;
    font-size: 20px; color: var(--white); letter-spacing: .5px;
  }
  .brand-mark { width: 11px; height: 11px; border-radius: 50%; background: var(--white); }
  .company {
    position: absolute; left: 34px; top: 180px;
    font-size: 15px; line-height: 20px; font-weight: 700; color: var(--white);
  }

  .services {
    position: absolute; left: 30px; top: 40px;
    list-style: none; font-size: 15px; line-height: 23.5px; color: var(--ink-soft);
  }
  .services li { display: flex; align-items: center; gap: 12px; }
  .services li::before {
    content: ""; width: 7px; height: 7px; background: var(--ink); flex: none;
  }
  .back-brand {
    position: absolute; right: 34px; bottom: 70px;
    display: flex; align-items: center; gap: 10px;
    font-family: "Cinzel", "Times New Roman", serif;
    font-size: 22px; color: var(--ink);
  }
  .back-brand-mark { width: 12px; height: 12px; border: 1.5px solid var(--ink); }
</style>
</head>
<body>
<main class="canvas">

  <section class="card card--front" aria-label="Business card front">
    <svg class="front-shapes" viewBox="0 0 520 300" preserveAspectRatio="none">
      <polygon points="0,0 520,0 520,50 262,236 0,236" fill="var(--card-dark)"/>
      <polyline points="520,66 263,250 0,250" fill="none" stroke="var(--card-dark)" stroke-width="2"/>
    </svg>

    <h1 class="holder-name">MARCUS DELLING</h1>

    <ul class="contact-list">
      <li>858-471-6093
        <svg viewBox="0 0 12 12"><path d="M2.5 1h2l1 3-1.3 1a6 6 0 0 0 2.8 2.8L8 6.5l3 1v2A1.5 1.5 0 0 1 9.5 11C5 11 1 7 1 2.5A1.5 1.5 0 0 1 2.5 1z" fill="var(--ink)"/></svg>
      </li>
      <li>info@brightoakbuilders.com
        <svg viewBox="0 0 12 12"><rect x="1" y="2.5" width="10" height="7" fill="var(--ink)"/><polyline points="1.5,3 6,6.5 10.5,3" fill="none" stroke="var(--white)" stroke-width="1"/></svg>
      </li>
      <li>www.brightoakbuilders.com
        <svg viewBox="0 0 12 12"><circle cx="6" cy="6" r="5" fill="var(--ink)"/><ellipse cx="6" cy="6" rx="2" ry="5" fill="none" stroke="var(--white)" stroke-width=".8"/><line x1="1" y1="6" x2="11" y2="6" stroke="var(--white)" stroke-width=".8"/></svg>
      </li>
    </ul>

    <div class="brand"><span class="brand-mark"></span>Harborline Builders</div>

    <p class="company">Harborline Builders Inc.<br>Licensed General Contractors</p>
  </section>

  <section class="card card--back" aria-label="Business card back">
    <ul class="services">
      <li>Remodel : Kitchen &amp; Bath</li>
      <li>Painting : Interior &amp; Exterior</li>
      <li>Flooring : Carpet, Vinyl, Wood</li>
      <li>Window &amp; Door Replacement</li>
      <li>Plumbing : Repairs &amp; Upgrades</li>
      <li>Energy- Efficient Upgrades</li>
      <li>Deck &amp; Pation Construction</li>
      <li>Water &amp; Mold Damage</li>
      <li>Garage Renovation</li>
    </ul>
    <div class="back-brand"><span class="back-brand-mark"></span>Harborline</div>
  </section>

</main>
</body>
</html>
```